Social Media App Needs PPT Template

We need a PowerPoint template for a new social media company based in the DC area called "Bold Ledger." We provide an interactive digital platform for executives to share actionable advice. We would like to see designs that use our orange logo color as an accent, but are mainly grey, white, and black. The final design should communicate clean, chic, modern, and professional.

Target Market(s)

Executives

Industry/Entity Type

Information Technology

Font styles to use
Sans Serif

Colors
f78f20
fbe7d2
ffffff
000000
e8e8e8
757575

Requirements
Must have
• My project must have title page and many options for the body of the ppt (graphs, tables, etc). It also needs to be easy to modify. I must have someone who is experienced in creating powerpoint templates.
Nice to have
• It would be nice to have a very modern and clean design that includes the logo on every page, but still leaves a lot of room for the content of the slide
Should not have
• My design project should not look to busy.

```html
<!DOCTYPE html>
<html lang="en">
<head>
<meta charset="utf-8">
<title>Bold Ledger – About Our Company</title>
<link href="https://fonts.googleapis.com/css2?family=Lato:ital,wght@0,300;0,400;0,700;1,700&display=swap" rel="stylesheet">
<style>
  :root {
    --board: #545454;
    --orange: #e8861a;
    --orange-light: #f0952a;
    --orange-text: #f08a14;
    --navy: #232b38;
    --paper: #f7f7f7;
    --paper-edge: #ececec;
    --ink: #4a4a4a;
    --white: #ffffff;
    --photo-dark: #151515;
    --photo-mid: #2c2f3a;
  }
  * { margin: 0; padding: 0; box-sizing: border-box; }
  html, body { width: 1200px; height: 960px; overflow: hidden; }
  body {
    background: var(--board);
    font-family: "Lato", sans-serif;
    position: relative;
  }
  .page-label {
    position: absolute;
    top: 74px; left: 0; width: 1172px;
    text-align: center;
    color: var(--white);
    font-weight: 300;
    font-size: 27px;
  }
  .slide {
    position: absolute;
    left: 111px; top: 135px;
    width: 970px; height: 728px;
    background: radial-gradient(ellipse at 50% 45%, var(--white) 0%, var(--paper) 55%, var(--paper-edge) 100%);
    overflow: hidden;
  }
  .slide-bands { position: absolute; inset: 0; width: 970px; height: 728px; }
  .slide-title {
    position: absolute;
    left: 30px; top: 62px;
    color: var(--white);
    font-weight: 300;
    font-size: 37px;
    letter-spacing: 0.2px;
  }
  .brand {
    position: absolute;
    left: 786px; top: 71px;
    display: flex; align-items: center; gap: 9px;
  }
  .brand-dot { width: 20px; height: 20px; border-radius: 50%; background: var(--orange-light); }
  .brand-name { color: var(--white); font-weight: 700; font-size: 22px; }
  .column {
    position: absolute;
    top: 202px;
    color: var(--ink);
    font-size: 15.2px;
    line-height: 19.4px;
    text-align: justify;
    hyphens: auto;
  }
  .column-left { left: 34px; width: 433px; }
  .column-right { left: 507px; width: 418px; }
  .column p + p { margin-top: 19.4px; }
  .lead {
    color: var(--orange-text);
    font-weight: 700;
    font-style: italic;
    font-size: 16.8px;
    line-height: 21px;
  }
  .photo {
    position: absolute;
    left: 510px; top: 351px;
    width: 415px; height: 263px;
    background: radial-gradient(ellipse at 35% 60%, #5b5f7a 0%, var(--photo-mid) 35%, var(--photo-dark) 80%);
  }
  .footer-text {
    position: absolute;
    left: 26px; top: 695px;
    color: var(--white);
    font-size: 13px;
  }
  .footer-text .sep { margin: 0 6px; }
</style>
</head>
<body>
  <div class="page-label">Page 3</div>

  <section class="slide">
    <svg class="slide-bands" viewBox="0 0 1212 910" aria-hidden="true">
      <polygon points="942,41 1212,41 1212,51 932,51" fill="var(--orange)"/>
      <polygon points="0,57 922,57 827,152 0,152" fill="var(--orange)"/>
      <polygon points="730,57 922,57 860,120 650,132" fill="var(--orange-light)" opacity="0.55"/>
      <polygon points="930,57 1212,57 1212,152 830,152" fill="var(--navy)"/>
      <polygon points="0,157 818,157 806,169 0,169" fill="var(--navy)"/>
      <polygon points="0,861 346,861 311,896 0,896" fill="var(--navy)"/>
      <polygon points="356,861 1212,861 1212,896 321,896" fill="var(--orange)"/>
    </svg>

    <h1 class="slide-title">About Our Company</h1>

    <div class="brand">
      <span class="brand-dot"></span>
      <span class="brand-name">Bold Ledger</span>
    </div>

    <div class="column column-left">
      <p class="lead">Lorem ipsum dolor sit amet, consectetuer adipiscing elit, sed diam nonummy nibh euismod tincidunt ut laoreet dolore magna aliquam erat volutpat. Ut wisi enim ad minim veniam, quis nostrud exerci tation ullamcorper suscipit lobortis nisl ut aliquip ex ea commodo consequat.</p>
      <p>Duis autem vel eum iriure dolor in hendrerit in vulputate velit esse molestie consequat, vel illum dolore eu feugiat nulla facilisis at vero eros et accumsan et iusto odio dignissim qui blandit praesent luptatum zzril delenit augue duis dolore te feugait nulla facilisi. Nam liber tempor cum soluta nobis eleifend option congue nihil imperdiet doming id quod mazim placerat facer possim assum. Typi non habent claritatem insitam; est usus legentis in iis qui facit eorum claritatem. Investigationes demonstraverunt lectores legere me lius quod ii legunt saepius. Claritas est etiam processus dynamicus, qui sequitur mutationem consuetudium lectorum.</p>
      <p>Typi non habent claritatem insitam; est usus legentis in iis qui facit eorum claritatem. Investigationes.</p>
    </div>

    <div class="column column-right">
      <p>Duis autem vel eum iriure dolor in hendrerit in vulputate velit esse molestie consequat, vel illum dolore eu feugiat nulla facilisis at vero eros et accumsan et iusto odio dignissim qui blandit praesent luptatum zzril delenit augue duis dolore te feugait nulla facilisi. Nam liber tempor cum soluta nobis eleifend option congue nihil imperdiet doming id quod mazim placerat facer possim assum.</p>
    </div>

    <div class="photo" role="img" aria-label="Photo of a businessman in a dark suit holding a smartphone with glowing social media icons floating above it"></div>

    <div class="footer-text">www.boldledger.com<span class="sep">|</span>Page 1</div>
  </section>
</body>
</html>
```